RWT Fittings Ltd Business Cards

We need a business card with our business logo. We provide window and door installations on high-rises in west coast British Colombia, Canada.

I would like my business information and details on one side of the card, and the other side the company name with logo

Target Market(s)

General Contractors

Industry/Entity Type

Construction

Contact Information for Business Card

one side i want my company name and logo in the dark theme logo that i provided

Requirements
Must have
• Marco Peltieri, 16045518293, RWTFittings@mailbox-demo.com, 1407-5194 Linden Row Burnaby BC, V5H 2K9, Owner & Manager

```html
<!DOCTYPE html>
<html lang="en">
<head>
<meta charset="utf-8">
<title>RWT Fittings Ltd – Business Cards</title>
<link rel="stylesheet" href="https://fonts.googleapis.com/css2?family=Open+Sans:wght@400;600;700&display=swap">
<style>
  :root {
    --stage: #232323;
    --card: #1f2024;
    --card-edge: #17181b;
    --accent: #2ea3df;
    --name-grey: #9a9b9f;
    --text-light: #f2f2f2;
    --pattern-dark: #141517;
    --pattern-light: #c9c9c9;
  }
  * { margin: 0; padding: 0; box-sizing: border-box; }
  html, body {
    width: 1200px; height: 780px; overflow: hidden;
    background: var(--stage);
    font-family: "Open Sans", Arial, sans-serif;
  }
  .canvas {
    position: relative; width: 1200px; height: 780px;
    display: flex; align-items: center; justify-content: center; gap: 60px;
  }
  .card {
    position: relative; width: 500px; height: 286px;
    background: var(--card);
    box-shadow: 0 0 0 1px var(--card-edge), 0 18px 40px rgba(0,0,0,.45);
    overflow: hidden;
  }
  /* front side */
  .card--front::before {
    content: ""; position: absolute; inset: 0;
    background: linear-gradient(115deg, transparent 52%, rgba(0,0,0,.28) 53%, transparent 62%);
  }
  .identity { position: absolute; left: 40px; top: 46px; }
  .identity__name { font-size: 27px; font-weight: 700; letter-spacing: .2px; line-height: 1.1; }
  .identity__first { color: var(--accent); }
  .identity__last { color: var(--name-grey); }
  .identity__role { margin-top: 4px; padding-left: 34px; font-size: 15px; color: var(--text-light); }
  .address {
    position: absolute; left: 40px; bottom: 38px;
    font-size: 14px; color: var(--text-light); line-height: 1.4;
  }
  .contact { position: absolute; left: 240px; top: 140px; list-style: none; }
  .contact__item {
    display: flex; align-items: center; gap: 9px;
    font-size: 14px; color: var(--text-light); line-height: 1.6;
    white-space: nowrap;
  }
  .contact__item:nth-child(2) { margin-left: -14px; }
  .contact__item:nth-child(3) { margin-left: -28px; }
  .contact__icon { width: 14px; height: 14px; flex: none; fill: var(--accent); }
  /* back side */
  .brand-pattern {
    position: absolute; inset: 0;
    background: linear-gradient(300deg, var(--pattern-light) 0%, #6f6f72 14%, #2a2b2f 34%, var(--pattern-dark) 60%);
  }
  .brand-name {
    position: absolute; left: 300px; top: 200px;
    display: flex; align-items: center; gap: 8px;
    font-size: 16px; font-weight: 700; color: var(--accent);
  }
  .brand-name__square { width: 12px; height: 12px; background: var(--accent); }
</style>
</head>
<body>
<main class="canvas">
  <section class="card card--front" aria-label="Card front">
    <div class="identity">
      <p class="identity__name"><span class="identity__first">Marco</span> <span class="identity__last">Peltieri</span></p>
      <p class="identity__role">Owner &amp; Manager</p>
    </div>
    <ul class="contact">
      <li class="contact__item">
        <svg class="contact__icon" viewBox="0 0 24 24" aria-hidden="true"><path d="M6.6 10.8a15.1 15.1 0 0 0 6.6 6.6l2.2-2.2a1 1 0 0 1 1-.25 11.4 11.4 0 0 0 3.6.57 1 1 0 0 1 1 1V20a1 1 0 0 1-1 1A17 17 0 0 1 3 4a1 1 0 0 1 1-1h3.5a1 1 0 0 1 1 1c0 1.25.2 2.45.57 3.57a1 1 0 0 1-.25 1z"/></svg>
        1 (604) 551-8293
      </li>
      <li class="contact__item">
        <svg class="contact__icon" viewBox="0 0 24 24" aria-hidden="true"><path d="M3 5h18a1 1 0 0 1 1 1v12a1 1 0 0 1-1 1H3a1 1 0 0 1-1-1V6a1 1 0 0 1 1-1zm9 7.5L4 7.3V9l8 5.2L20 9V7.3z"/></svg>
        RWTFittings@mailbox-demo.com
      </li>
      <li class="contact__item">
        <svg class="contact__icon" viewBox="0 0 24 24" aria-hidden="true"><circle cx="12" cy="12" r="10"/></svg>
        www.rwtfittings-demo.com
      </li>
    </ul>
    <p class="address">1407-5194 Linden Row Burnaby BC, V5H 2K9</p>
  </section>

  <section class="card card--back" aria-label="Card back">
    <div class="brand-pattern" role="img" aria-label="Repeating company mark pattern fading from black to silver"></div>
    <p class="brand-name"><span class="brand-name__square"></span>RWT Fittings Ltd</p>
  </section>
</main>
</body>
</html>
```